Quiet Harbor Podcast W/ Dr. Lena Marsh

Podcast Cover Art. I am in search of a re-design for my existing podcast. We have over 100 episodes, but I want to change the name to Quiet Harbor Podcast With Dr. Lena Marsh. I'm open to any ideas, and have attached source file image to use. ( note: NO brain images please).

```html
<!DOCTYPE html>
<html lang="en">
<head>
<meta charset="utf-8">
<title>Quiet Harbor Podcast With Dr. Lena Marsh</title>
<link rel="stylesheet" href="https://fonts.googleapis.com/css2?family=Bebas+Neue&display=swap">
<style>
  :root {
    --navy: #1e2130;
    --brick: #d64b35;
    --cream: #f8eee8;
    --jacket: #e2573d;
    --jacket-light: #f07a5c;
    --shirt: #efe4dc;
  }
  html, body {
    margin: 0;
    padding: 0;
    width: 1200px;
    height: 1200px;
    overflow: hidden;
    background: var(--navy);
  }
  .cover {
    position: relative;
    width: 1200px;
    height: 1200px;
    background: var(--navy);
    font-family: "Bebas Neue", "Arial Narrow", sans-serif;
  }
  .cover-art {
    position: absolute;
    inset: 0;
  }
  .show-title {
    fill: var(--brick);
    font-size: 158px;
    letter-spacing: 2px;
  }
  .show-kind {
    fill: var(--cream);
    font-size: 64px;
    letter-spacing: 22px;
  }
  .host-line {
    position: absolute;
    left: 0;
    right: 0;
    top: 1078px;
    margin: 0;
    text-align: center;
    font-size: 76px;
    line-height: 1;
    font-weight: 400;
    color: var(--cream);
    letter-spacing: 1px;
  }
  .host-line .lead {
    color: var(--brick);
  }
</style>
</head>
<body>
<main class="cover">
  <svg class="cover-art" width="1200" height="1200" viewBox="0 0 1200 1200" xmlns="http://www.w3.org/2000/svg">
    <defs>
      <path id="title-arc" d="M 130 646 A 470 470 0 0 1 1070 646"/>
      <linearGradient id="portrait-fill" x1="0" y1="0" x2="0" y2="1">
        <stop offset="0" stop-color="#c99a72"/>
        <stop offset="0.45" stop-color="#e8b9a0"/>
        <stop offset="0.6" stop-color="var(--jacket-light)"/>
        <stop offset="1" stop-color="var(--jacket)"/>
      </linearGradient>
    </defs>

    <text class="show-title" text-anchor="middle">
      <textPath href="#title-arc" startOffset="50%">QUIET HARBOR</textPath>
    </text>

    <text class="show-kind" x="611" y="278" text-anchor="middle">PODCAST</text>

    <circle class="host-portrait" cx="608" cy="680" r="358" fill="url(#portrait-fill)"
            role="img" aria-label="Illustrated portrait of the host in an orange windowpane blazer and white shirt"/>
  </svg>

  <h1 class="host-line"><span class="lead">WITH</span> DR. LENA MARSH</h1>
</main>
</body>
</html>
```